New business card/stationary for a consulting company

I am looking for a clean and very professional looking business card for my consulting company as well as corresponding stationary. I am uploading our logo. I like simple and powerful for the feel. No graphics but I am open on everything else. Below is my contact information but would like the final to be in a version I can add my employees information into and print. Thank you.

Daniel Whitcombe
dan@ferncliffadvisory.com
2870 North 9th Avenue, Summit Floor, Elm Ridge, Illinois 60531
www.ferncliffadvisory.com

Industry/Entity Type

Consulting

Contact Information for Business Card

Daniel Whitcombe
dan@ferncliffadvisory.com
www.ferncliffadvisory.com

Font styles to use
Serif
Sans Serif

Requirements
Must have
• Our logo and the business card details.
Nice to have
• our website www.ferncliffadvisory.com

```html
<!DOCTYPE html>
<html lang="en">
<head>
<meta charset="utf-8">
<title>Daniel Whitcombe – Ferncliff Advisory Business Card</title>
<link rel="stylesheet" href="https://fonts.googleapis.com/css2?family=Marcellus&family=Roboto:wght@400&display=swap">
<style>
  :root {
    --backdrop: #d8d3cb;
    --card: #eef0f0;
    --card-edge: #d3d6d7;
    --navy: #1d2a4d;
    --ink: #2b2b2e;
  }
  * { margin: 0; padding: 0; box-sizing: border-box; }
  html, body {
    width: 1200px;
    height: 970px;
    overflow: hidden;
    background: var(--backdrop);
  }
  .business-card {
    position: absolute;
    left: 100px;
    top: 207px;
    width: 1000px;
    height: 556px;
    background: var(--card);
    border: 1px solid var(--card-edge);
    border-radius: 4px;
    box-shadow: 0 14px 40px rgba(40, 36, 30, 0.18);
  }
  .holder-name {
    position: absolute;
    left: 48px;
    top: 68px;
    font-family: "Marcellus", serif;
    font-size: 35px;
    letter-spacing: 2.5px;
    color: var(--navy);
    text-transform: uppercase;
    line-height: 1;
  }
  .contact-list {
    position: absolute;
    left: 48px;
    top: 366px;
    list-style: none;
    font-family: "Roboto", sans-serif;
    font-size: 22px;
    color: var(--ink);
    line-height: 37px;
  }
  .contact-item {
    display: flex;
    align-items: center;
    gap: 20px;
  }
  .contact-icon {
    width: 22px;
    height: 22px;
    flex: none;
  }
  .postal-address {
    margin-top: 2px;
    line-height: 37px;
  }
  .brand-name {
    position: absolute;
    right: 58px;
    bottom: 68px;
    display: flex;
    align-items: center;
    gap: 14px;
    font-family: "Marcellus", serif;
    font-size: 27px;
    letter-spacing: 2px;
    color: var(--navy);
    text-transform: uppercase;
  }
  .brand-square {
    width: 20px;
    height: 20px;
    background: var(--navy);
  }
</style>
</head>
<body>
  <section class="business-card">
    <h1 class="holder-name">Daniel Whitcombe</h1>

    <ul class="contact-list">
      <li class="contact-item">
        <svg class="contact-icon" viewBox="0 0 22 22" aria-hidden="true">
          <rect x="2" y="5" width="18" height="12" fill="var(--navy)"/>
          <path d="M2 5 L11 12 L20 5" fill="none" stroke="var(--card)" stroke-width="1.6"/>
          <path d="M2 17 L8.5 10.5 M20 17 L13.5 10.5" stroke="var(--card)" stroke-width="1.2"/>
        </svg>
        <span>dan@ferncliffadvisory.com</span>
      </li>
      <li class="contact-item">
        <svg class="contact-icon" viewBox="0 0 22 22" aria-hidden="true">
          <circle cx="11" cy="11" r="8" fill="none" stroke="var(--navy)" stroke-width="1.8"/>
          <ellipse cx="11" cy="11" rx="3.5" ry="8" fill="none" stroke="var(--navy)" stroke-width="1.5"/>
          <line x1="3" y1="11" x2="19" y2="11" stroke="var(--navy)" stroke-width="1.5"/>
        </svg>
        <span>www.ferncliffadvisory.com</span>
      </li>
      <li class="postal-address">2870 North 9th Avenue, Summit<br>Floor, Elm Ridge, Illinois 60531</li>
    </ul>

    <div class="brand-name">
      <span class="brand-square"></span>
      <span>Ferncliff Advisory</span>
    </div>
  </section>
</body>
</html>
```